Animal Eye Clinic needs a Business card

We are a new veterinary ophthalmology practice (Ridgeline Pet Vision Care) and we need a business card designed. We only see animal eyes - we are not a regular veterinary clinic. We already have a logo. We are looking for a professional, good looking business card to hand out to our clients. We are looking for something simple but professional and contemporary. Our logo is likely the only picture/graphic that needs to be on the card.
Updates

Contact Information for Business Card

Delia Vossman, BSc, DVM, MSc, DipACVO
Veterinary Ophthalmologist

Phone: 250.418.3927
Email: ridgelinepetvisioncare@mailbox-example.net
Website: ridgelinepetvisioncare-example.net
Address: 1874 Thornbury Rd
Kelowna, BC, V1X 4M9

Colors

Designer to choose colors to be used in the design.

Requirements
Must have
• Our logo (attached)

```html
<!DOCTYPE html>
<html lang="en">
<head>
<meta charset="utf-8">
<title>Ridgeline Pet Vision Care – Business Card</title>
<link rel="stylesheet" href="https://fonts.googleapis.com/css2?family=Lato:wght@400;700;900&display=swap">
<style>
  :root {
    --teal: #1e9aab;
    --grey: #777878;
    --grey-text: #6b6b6b;
    --white: #ffffff;
    --backdrop: #2e2f31;
  }
  * { margin: 0; padding: 0; box-sizing: border-box; }
  html, body { width: 1200px; height: 900px; overflow: hidden; }
  body {
    background: var(--backdrop);
    font-family: "Lato", Arial, sans-serif;
    position: relative;
  }
  .card {
    position: absolute;
    left: 290px;
    width: 620px;
    height: 354px;
    border-radius: 18px;
    overflow: hidden;
  }
  .card-front { top: 48px; background: var(--grey); }
  .card-back { top: 446px; background: var(--white); }
  .card-shapes { position: absolute; inset: 0; width: 100%; height: 100%; }

  .brand {
    position: absolute;
    display: flex;
    align-items: center;
    gap: 12px;
    font-weight: 900;
    letter-spacing: 0.2px;
    white-space: nowrap;
  }
  .brand-dot { border-radius: 50%; flex: none; }
  .card-front .brand { left: 112px; top: 150px; font-size: 27px; color: var(--white); }
  .card-front .brand-dot { width: 40px; height: 40px; background: var(--white); }
  .card-back .brand { left: 40px; top: 125px; font-size: 22px; color: var(--teal); }
  .card-back .brand-dot { width: 32px; height: 32px; background: var(--teal); }

  .person {
    position: absolute;
    right: 40px;
    top: 36px;
    text-align: right;
  }
  .person-name { font-size: 27px; font-weight: 900; color: var(--teal); line-height: 1.05; }
  .person-credentials { font-size: 10.5px; color: var(--grey-text); margin-top: 2px; }
  .person-title { font-size: 15px; color: var(--grey-text); margin-top: 3px; }

  .contact {
    position: absolute;
    right: 20px;
    top: 198px;
    text-align: right;
    color: var(--white);
    font-size: 12px;
    line-height: 1.45;
    font-style: normal;
  }
  .contact-address { margin-right: 24px; margin-bottom: 4px; }
  .contact-line { display: flex; justify-content: flex-end; align-items: center; gap: 8px; }
  .contact-line svg { width: 16px; height: 16px; flex: none; }
</style>
</head>
<body>

<section class="card card-front" aria-label="Business card front">
  <svg class="card-shapes" viewBox="0 0 620 354" preserveAspectRatio="none" aria-hidden="true">
    <path fill="var(--teal)" d="M190,0 C120,70 85,160 88,250 C230,330 430,330 620,290 L620,0 Z"/>
  </svg>
  <div class="brand"><span class="brand-dot"></span>Ridgeline Pet Vision Care</div>
</section>

<section class="card card-back" aria-label="Business card back">
  <svg class="card-shapes" viewBox="0 0 620 354" preserveAspectRatio="none" aria-hidden="true">
    <path fill="none" stroke="var(--grey)" stroke-width="11" d="M-5,288 C170,288 245,268 312,205 C380,142 445,124 530,120"/>
    <path fill="var(--teal)" d="M0,305 C170,305 250,285 320,220 C390,155 460,135 620,128 L620,354 L0,354 Z"/>
  </svg>

  <div class="brand"><span class="brand-dot"></span>Ridgeline Pet Vision Care</div>

  <div class="person">
    <div class="person-name">Delia Vossman,</div>
    <div class="person-credentials">BSc, DVM, MSc, DipACVO</div>
    <div class="person-title">Veterinary Ophthalmologist</div>
  </div>

  <address class="contact">
    <div class="contact-address">1874 Thornbury Rd<br>Kelowna, BC, V1X 4M9</div>
    <div class="contact-line">250.418.3927
      <svg viewBox="0 0 16 16" aria-hidden="true"><path fill="var(--white)" d="M4 1.5l2 3-1.3 1.3c.8 1.8 2.2 3.2 4 4L10 8.5l3 2-1 2.5c-.4.8-1.3 1-2 .8C5.8 12.6 3.4 10.2 2.2 6c-.2-.7 0-1.6.8-2z"/></svg>
    </div>
    <div class="contact-line">ridgelinepetvisioncare@mailbox-example.net
      <svg viewBox="0 0 16 16" aria-hidden="true"><rect x="1.5" y="3.5" width="13" height="9" fill="var(--white)"/><path d="M1.5 3.5l6.5 5 6.5-5" fill="none" stroke="var(--teal)" stroke-width="1.2"/></svg>
    </div>
    <div class="contact-line">ridgelinepetvisioncare-example.net
      <svg viewBox="0 0 16 16" aria-hidden="true"><g fill="none" stroke="var(--white)" stroke-width="1.2"><circle cx="8" cy="8" r="6.3"/><ellipse cx="8" cy="8" rx="2.8" ry="6.3"/><path d="M1.7 8h12.6M2.8 4.7h10.4M2.8 11.3h10.4"/></g></svg>
    </div>
  </address>
</section>

</body>
</html>
```